Quillmere Air Business Card Design

Design new, 2 sides, business cards for a residential and light commercial heating, air conditioning contractor.

Target Market(s)

Homeowners, small businesses

Industry/Entity Type

Business

Contact Information for Business Card

Dominic Westerhall
Phone - 862-415-2736
Email
Address - PO box 518
Brightwater NJ 07912
Website - www.QuillmereAirLLC.example

Requirements
Must have
• logo, company colors, standard size with no die cut, so I can use nova stamp

```html
<!DOCTYPE html>
<html lang="en">
<head>
<meta charset="utf-8">
<title>Quillmere Air Business Card</title>
<link href="https://fonts.googleapis.com/css2?family=Barlow:wght@400;500;600;700&display=swap" rel="stylesheet">
<style>
  :root {
    --backdrop: #e3e3e3;
    --card: #f4f4f2;
    --burgundy: #7d2333;
    --gold: #f2cd62;
    --icon-red: #c4262e;
    --ink: #3b2a2e;
    --name-ink: #4a2128;
  }
  * { margin: 0; padding: 0; box-sizing: border-box; }
  html, body {
    width: 1200px; height: 576px; overflow: hidden;
    background: var(--backdrop);
    font-family: "Barlow", sans-serif;
  }
  .canvas { position: relative; width: 1200px; height: 576px; }
  .card {
    position: absolute; top: 138px;
    width: 484px; height: 293px;
    background: var(--card);
    overflow: hidden;
  }
  .card--front { left: 81px; }
  .card--back { left: 602px; }

  .brand {
    position: absolute;
    display: flex; align-items: center;
    color: var(--burgundy);
    font-weight: 700;
    white-space: nowrap;
    transform: translate(-50%, -50%);
  }
  .brand__dot { border-radius: 50%; background: var(--burgundy); flex: none; }
  .card--front .brand { left: 50%; top: 134px; font-size: 40px; gap: 12px; }
  .card--front .brand__dot { width: 26px; height: 26px; }
  .card--back .brand { left: 126px; top: 144px; font-size: 24px; gap: 8px; }
  .card--back .brand__dot { width: 16px; height: 16px; }

  .service-band {
    position: absolute; left: 0; right: 0; top: 247px; height: 26px;
    background: var(--burgundy);
    color: var(--gold);
    font-size: 12.5px; font-weight: 400;
    display: flex; align-items: center; justify-content: center;
  }
  .service-band__sep { margin: 0 6px; }

  .contact { position: absolute; left: 254px; top: 80px; color: var(--ink); }
  .contact__name { font-size: 17px; line-height: 20px; font-weight: 600; color: var(--name-ink); letter-spacing: 0.2px; }
  .contact__title { font-size: 11.5px; line-height: 14px; margin-top: 3px; }
  .contact__list { list-style: none; margin-top: 20px; }
  .contact__item {
    display: flex; align-items: center; gap: 8px;
    font-size: 12px; line-height: 16.5px;
  }
  .contact__icon { width: 11px; height: 11px; flex: none; fill: var(--icon-red); }

  .base-stripe {
    position: absolute; left: 0; right: 0; bottom: 0; height: 6px;
    background: var(--burgundy);
  }
</style>
</head>
<body>
<main class="canvas">
  <section class="card card--front" aria-label="Card front">
    <div class="brand"><span class="brand__dot"></span>Quillmere Air</div>
    <div class="service-band">
      Residential &amp; Light Commercial Heating<span class="service-band__sep">•</span>Air Conditioning Contractor
    </div>
  </section>

  <section class="card card--back" aria-label="Card back">
    <div class="brand"><span class="brand__dot"></span>Quillmere Air</div>
    <div class="contact">
      <p class="contact__name">Dominic Westerhall</p>
      <p class="contact__title">Managing Director</p>
      <ul class="contact__list">
        <li class="contact__item">
          <svg class="contact__icon" viewBox="0 0 12 12" aria-hidden="true"><path d="M1 4c0-2 2-3 5-3s5 1 5 3v1H8V4H4v1H1z"/><path d="M3 6h6l1.5 5h-9z"/></svg>
          862-415-2736
        </li>
        <li class="contact__item">
          <svg class="contact__icon" viewBox="0 0 12 12" aria-hidden="true"><path d="M0 2h12v8H0z M1 3l5 4 5-4" stroke="#f4f4f2" stroke-width="1"/></svg>
          info@QuillmereAirLLC.example
        </li>
        <li class="contact__item">
          <svg class="contact__icon" viewBox="0 0 12 12" aria-hidden="true"><circle cx="6" cy="6" r="5.5"/><path d="M0.5 6h11M6 0.5v11M6 0.5c-3 3-3 8 0 11M6 0.5c3 3 3 8 0 11" stroke="#f4f4f2" stroke-width="0.8" fill="none"/></svg>
          www.QuillmereAirLLC.example
        </li>
        <li class="contact__item">
          <svg class="contact__icon" viewBox="0 0 12 12" aria-hidden="true"><path d="M6 0a4.2 4.2 0 0 1 4.2 4.2C10.2 7.5 6 12 6 12S1.8 7.5 1.8 4.2A4.2 4.2 0 0 1 6 0z"/><circle cx="6" cy="4.2" r="1.6" fill="#f4f4f2"/></svg>
          PO box 518 Brightwater NJ 07912
        </li>
      </ul>
    </div>
    <div class="base-stripe"></div>
  </section>
</main>
</body>
</html>
```